Healthy lifestyle Influencer business card

I need your creativity to have a business card that I can leave in all the restaurants, hotels and spas I visit to inform them that I am an influencer specializing in the wellness sector and that I will write a review about them. You can use my instagram photos Lunavita27 or on my website www.piattileggeriorto.it. I would like my business card to impress with its creativity! thank you very much!

Contact Information for Business Card

siteweb, instagram, phone number

Font styles to use
Decorative
Script

Colors
0094D4
00A9DD
6FCCEA
C7EBF8
E9F6FB
59FF00
82FF00
B8FF75
E3FFCB
F4FFEA
FFC000
F8CF3A
FAE287
FDF2CF
FEFAEE
F0912C
F2A743
F7CA91
FBE8D2
FDF5EE
EE7325
F08F49
F5BC92
FAE3D3
FDF4ED
EB3D1F
EC4F4E
F09395
F8D3D4
FCEDEE
E54698
E96AAD
F1A4CE
F9D9EA
FCEFF6

Requirements
Nice to have
• creativity

```html
<!DOCTYPE html>
<html lang="it">
<head>
<meta charset="utf-8">
<title>Luna Vita Chef – Biglietto da visita</title>
<link href="https://fonts.googleapis.com/css2?family=Ubuntu:wght@400&family=Ubuntu+Condensed&family=Roboto:wght@300&display=swap" rel="stylesheet">
<style>
  :root {
    --backdrop: #2f2f2f;
    --sage: #8fb5aa;
    --sage-light: #9dc0b6;
    --sage-dark: #8aafa5;
    --charcoal: #4a4a4a;
    --band: #4d4d4d;
    --paper: #f1f1f1;
    --paper-shade: #e6e6e6;
    --text: #4a4a4a;
  }
  * { margin: 0; padding: 0; box-sizing: border-box; }
  html, body { width: 1200px; height: 1138px; overflow: hidden; }
  body { background: var(--backdrop); position: relative; }

  .card {
    position: absolute;
    border-radius: 16px;
    overflow: hidden;
  }

  /* Front side */
  .card--front {
    left: 272px; top: 184px; width: 622px; height: 376px;
    background: linear-gradient(180deg, var(--sage-light), var(--sage-dark));
  }
  .photo-tile { position: absolute; width: 185px; height: 104px; }
  .photo-tile--mousse    { left: 24px;  top: 22px;  background: linear-gradient(135deg, #ecebee, #b9a09a); }
  .photo-tile--redvelvet { left: 219px; top: 22px;  background: linear-gradient(135deg, #d9c6bd, #b3564a); }
  .photo-tile--berries   { left: 415px; top: 22px;  background: linear-gradient(135deg, #6b5440, #3e4f7a); }
  .photo-tile--tart      { left: 24px;  top: 135px; background: linear-gradient(135deg, #4c5468, #d9cfd6); }
  .photo-tile--batter    { left: 219px; top: 135px; background: linear-gradient(135deg, #8a5a2c, #c59373); }
  .photo-tile--coconut   { left: 415px; top: 135px; background: linear-gradient(135deg, #f1eeee, #dcbf92); }

  .front-brand__name {
    position: absolute; left: 0; width: 622px; top: 270px;
    font-family: 'Ubuntu', sans-serif; font-size: 35px; line-height: 1;
    text-align: center; color: var(--charcoal);
  }
  .front-brand__tagline {
    position: absolute; left: 0; width: 622px; top: 318px;
    font-family: 'Ubuntu', sans-serif; font-size: 13.5px; line-height: 1;
    text-align: center; color: var(--charcoal);
  }

  /* Back side */
  .card--back {
    left: 274px; top: 606px; width: 619px; height: 375px;
    background: linear-gradient(180deg, var(--paper), var(--paper-shade));
  }
  .back-waves { position: absolute; left: 0; top: 0; }
  .owner-name {
    position: absolute; right: 35px; top: 30px;
    font-family: 'Ubuntu Condensed', sans-serif;
    font-size: 31px; line-height: 1.2; color: var(--charcoal);
  }
  .back-brand__name {
    position: absolute; left: 16px; top: 160px;
    font-family: 'Ubuntu', sans-serif; font-size: 50px; line-height: 1; color: var(--charcoal);
  }
  .back-brand__tagline {
    position: absolute; left: 66px; top: 222px;
    font-family: 'Ubuntu', sans-serif; font-size: 18px; line-height: 1; color: var(--charcoal);
  }
  .contact-list {
    position: absolute; right: 35px; top: 270px; list-style: none;
    font-family: 'Roboto', sans-serif; font-weight: 300; font-size: 16px; color: var(--text);
  }
  .contact-list li {
    display: flex; align-items: center; justify-content: flex-end;
    gap: 22px; height: 24px;
  }
  .contact-list svg { width: 16px; height: 16px; flex: none; }
  .social {
    position: absolute; left: 36px; top: 319px;
    display: flex; align-items: center; gap: 57px;
    font-family: 'Roboto', sans-serif; font-weight: 300; font-size: 16px; color: var(--text);
  }
  .social__dot { width: 14px; height: 14px; border-radius: 50%; background: var(--sage); }
</style>
</head>
<body>

<section class="card card--front">
  <div class="photo-tile photo-tile--mousse" role="img" aria-label="Foto: coppe di mousse al cioccolato con cucchiaio"></div>
  <div class="photo-tile photo-tile--redvelvet" role="img" aria-label="Foto: torta red velvet tagliata"></div>
  <div class="photo-tile photo-tile--berries" role="img" aria-label="Foto: dessert in bicchiere con mirtilli e lamponi"></div>
  <div class="photo-tile photo-tile--tart" role="img" aria-label="Foto: cheesecake ai mirtilli"></div>
  <div class="photo-tile photo-tile--batter" role="img" aria-label="Foto: impasto al cioccolato in tortiera"></div>
  <div class="photo-tile photo-tile--coconut" role="img" aria-label="Foto: biscotti al cocco"></div>
  <div class="front-brand__name">Luna Vita Chef</div>
  <div class="front-brand__tagline">Leggera con i piatti del cuore</div>
</section>

<section class="card card--back">
  <svg class="back-waves" width="619" height="375" viewBox="0 0 619 375" aria-hidden="true">
    <path d="M0 0 H619 V120 C540 138 470 130 400 95 C320 50 230 20 120 30 C70 35 30 48 0 62 Z" fill="var(--sage)"/>
    <path d="M0 62 C60 30 160 10 250 20 C330 30 390 70 450 100 C510 128 570 128 619 118 V134 C560 152 500 152 440 127 C370 97 300 57 210 50 C120 44 50 67 0 90 Z" fill="var(--band)"/>
    <path d="M0 62 C40 45 90 35 140 30 C80 42 35 56 0 72 Z" fill="#ffffff" opacity="0.6"/>
    <path d="M619 134 V150 C560 167 495 162 430 132 C490 152 560 152 619 134 Z" fill="var(--band)"/>
  </svg>
  <div class="owner-name">Luna Ferrante</div>
  <div class="back-brand__name">Luna Vita Chef</div>
  <div class="back-brand__tagline">Leggera con i piatti del cuore</div>

  <div class="social">
    <span class="social__dot"></span>
    <span class="social__handle">@Lunavita27</span>
  </div>

  <ul class="contact-list">
    <li><span>000-0000-0000</span>
      <svg viewBox="0 0 16 16" aria-hidden="true"><path d="M2 5 C2 3 5 2 8 2 C11 2 14 3 14 5 V6 H11 V5 H5 V6 H2 Z M4 7 H12 L13 13 H3 Z" fill="var(--sage)"/><circle cx="8" cy="10" r="1.6" fill="#fff"/></svg>
    </li>
    <li><span>info@piattileggeriorto.it</span>
      <svg viewBox="0 0 16 16" aria-hidden="true"><rect x="1.5" y="3.5" width="13" height="9" fill="var(--sage)"/><path d="M1.5 3.5 L8 9 L14.5 3.5 M1.5 12.5 L6 7.5 M14.5 12.5 L10 7.5" stroke="#fff" stroke-width="1" fill="none"/></svg>
    </li>
    <li><span>www.piattileggeriorto.it</span>
      <svg viewBox="0 0 16 16" aria-hidden="true"><circle cx="8" cy="8" r="6.5" fill="var(--sage)"/><path d="M1.5 8 H14.5 M8 1.5 V14.5 M3 4.5 H13 M3 11.5 H13" stroke="#fff" stroke-width="0.8"/><ellipse cx="8" cy="8" rx="3" ry="6.5" stroke="#fff" stroke-width="0.8" fill="none"/></svg>
    </li>
  </ul>
</section>

</body>
</html>
```